Bookcover: Ways to Turn Into a Bold Pathfinder

I am publishing a super-low-cost innovation book for €4,99 on Quillmere Open Press to help everyone become a great innovator: young ambitious people without college education nor a big budget. Do you want to help me?

Brief:
Design a book cover 1600 x 2560 pixels for QOP.
Main title: Ways to Turn Into a Bold Pathfinder
Sub title: mindset - insights - skills & tools
Author: Joost ter Brakel
Design: captive, and appealing to everyone
Target Group: young ambitious people without college education

For quillmere please format the height/width ratio of 1.6:1

```html
<!DOCTYPE html>
<html lang="en">
<head>
<meta charset="utf-8">
<title>Ways to Turn Into a Bold Pathfinder — Book Cover</title>
<link href="https://fonts.googleapis.com/css2?family=Bebas+Neue&family=Oswald:wght@200&display=swap" rel="stylesheet">
<style>
  :root {
    --stage: #9e9c9d;
    --orange: #ff8c00;
    --ink: #000000;
    --footer: #231f20;
    --paper: #ffffff;
    --bulb-light: #f7d64a;
    --bulb-deep: #e9b51c;
  }
  html, body {
    margin: 0;
    padding: 0;
    width: 1200px;
    height: 1200px;
    overflow: hidden;
    background: var(--stage);
  }
  .cover {
    position: absolute;
    left: 295px;
    top: 141px;
    width: 617px;
    height: 925px;
    background: var(--orange);
    overflow: hidden;
  }
  .torn-band {
    position: absolute;
    left: 0;
    top: 442px;
    width: 617px;
    height: 176px;
    z-index: 1;
  }
  .book-title {
    margin: 0;
    position: absolute;
    inset: 0;
    z-index: 2;
  }
  .title-line {
    position: absolute;
    left: 32px;
    margin: 0;
    font-family: "Bebas Neue", "Arial Narrow", sans-serif;
    font-weight: 400;
    line-height: 1;
    color: var(--ink);
    white-space: nowrap;
    text-transform: uppercase;
  }
  .title-line--first { top: 24px; font-size: 158px; }
  .title-line--second { top: 163px; font-size: 124px; }
  .title-line--accent { top: 275px; font-size: 207px; }
  .title-line--keyword {
    top: 474px;
    font-size: 130px;
    color: var(--orange);
  }
  .idea-bulb {
    position: absolute;
    left: 421px;
    top: 279px;
    width: 137px;
    height: 150px;
    border-radius: 50% 50% 40% 40%;
    background: radial-gradient(circle at 50% 40%, var(--bulb-light), var(--bulb-deep) 70%, transparent 72%);
    z-index: 2;
  }
  .subtitle-rule {
    position: absolute;
    left: 32px;
    top: 637px;
    width: 5px;
    height: 144px;
    background: var(--ink);
  }
  .subtitle {
    position: absolute;
    left: 59px;
    top: 631px;
    margin: 0;
    font-family: "Oswald", "Arial Narrow", sans-serif;
    font-weight: 200;
    font-size: 72px;
    line-height: 72px;
    color: var(--ink);
    text-transform: uppercase;
    white-space: nowrap;
  }
  .author-bar {
    position: absolute;
    left: 0;
    bottom: 0;
    width: 617px;
    height: 116px;
    background: var(--footer);
  }
  .author {
    position: absolute;
    left: 32px;
    top: 37px;
    margin: 0;
    font-family: "Bebas Neue", "Arial Narrow", sans-serif;
    font-size: 53px;
    line-height: 1;
    color: var(--paper);
    white-space: nowrap;
  }
  .author__surname { color: var(--orange); }
</style>
</head>
<body>
  <main class="cover">
    <svg class="torn-band" viewBox="0 0 617 170" preserveAspectRatio="none" aria-hidden="true">
      <path fill="var(--paper)" d="M0 8 L20 4 L38 10 L55 5 L75 9 L96 3 L118 8 L140 6 L160 11 L182 5 L205 9 L228 6 L250 12 L272 7 L296 10 L318 4 L340 9 L362 6 L386 11 L410 5 L432 9 L455 6 L478 12 L500 7 L522 10 L545 5 L568 9 L590 6 L617 10 L617 160 L596 164 L574 158 L552 165 L530 160 L508 166 L485 159 L462 164 L440 158 L418 165 L396 160 L372 166 L350 159 L328 164 L305 158 L282 165 L260 161 L236 167 L214 160 L192 165 L170 159 L146 166 L124 160 L102 165 L80 158 L58 164 L36 160 L16 166 L0 162 Z"/>
      <path fill="var(--ink)" d="M0 26 L22 22 L44 28 L66 23 L90 27 L112 21 L136 26 L158 24 L180 29 L204 23 L226 27 L250 22 L272 28 L296 24 L320 27 L344 21 L366 26 L390 23 L414 28 L436 22 L460 26 L484 23 L508 29 L530 24 L554 27 L578 22 L600 26 L617 24 L617 146 L594 150 L570 145 L548 151 L524 146 L500 152 L478 145 L454 150 L432 144 L408 151 L386 146 L362 152 L340 145 L316 150 L294 144 L270 151 L248 147 L224 152 L202 146 L178 151 L156 145 L132 152 L110 146 L86 151 L64 144 L42 150 L20 146 L0 151 Z"/>
    </svg>

    <h1 class="book-title">
      <span class="title-line title-line--first">Ways to</span>
      <span class="title-line title-line--second">Turn into a</span>
      <span class="title-line title-line--accent">Bold</span>
      <span class="title-line title-line--keyword">Pathfinder</span>
    </h1>

    <div class="idea-bulb" role="img" aria-label="Illustration of a crumpled yellow paper light bulb with light rays"></div>

    <div class="subtitle-rule"></div>
    <p class="subtitle">Mindset - Insights -<br>Skills &amp; Tools</p>

    <footer class="author-bar">
      <p class="author">JOOST TER <span class="author__surname">BRAKEL</span></p>
    </footer>
  </main>
</body>
</html>
```